Bluefern Business Services needs a new interactive and interesting website

We need an interesting, professional, modern and functional company website for Bluefern Business Services - a young IT Services company based out of Chennai, India.

Bluefern Business Services is a fully owned subsidiary of Marlow Goods, one of the world's leading direct to consumer wine merchant.

We already have a registered company logo which must feature in the website.

We conceive, design, develop, test, implement and support IT solutions across the entire Marlow Goods IT landscape. For ex : We currently run about 25 e-commerce websites for Marlow Goods on ATG and Dot Net.

We would like to see our corporate colors used in the website. (Burgundy wine and wine green - source: www.bluefernbs-site.com)

We are looking at this website to communicate a fun, friendly and professionally managed company - reaching out to career seekers, prospective customers and general public.

For reference - The company name 'Bluefern' is an inspiration from the Marlow Goods lineage.

The second image with the world map is stickered on our main entrance to the office, I am not sure where this can be used -just putting it out there..

Please note that there are only a few more days to submit designs for this contest  !

I would appreciate if you can help posting your designs in time for our review and consideration.

Thanks.

Reason: Thanks for your inputs. We have a number of designers and a lot to digest and work with in the past few days. There has been a rush of new designs in the last few days Hence we will require more time to process these and make our decision. Hence i am requesting the contest to be open for more days. Regards, Tarun

Target Market(s)

Prospective job seekers who want to know more about the company and also wish to apply for a job vacancy
People wanting to know more about the company in general and our progress
People who want to see what we offer and how we can help them too - prospective customers
Companies that are interested in our IT Captive journey and are looking for a business opportunity

Industry/Entity Type

E-Commerce

Requirements
Must have
• Log In/ Register facility acting as a Single Sign on for Intranet (Employees)

Facility to post job vacancies (with an expiry date) and enable people to apply for a role and upload their CV/Resume.

Facility to Review Job applications

Facility for website visitors to contact Bluefern business Services via an online 'Contact Us' form with a split of job seekers and business opportunities

Gallery facility to upload pictures regarding company events
Nice to have
• Less Cluttered and contemporary design
Some Wine/Vineyard inspirations will be good but not too much, the company is an IT services company

```html
<!DOCTYPE html>
<html lang="en">
<head>
<meta charset="utf-8">
<title>Bluefern Business Services</title>
<link href="https://fonts.googleapis.com/css2?family=Open+Sans:wdth,wght@75..100,400..700&family=Arimo:wght@400;700&display=swap" rel="stylesheet">
<style>
:root{
  --burgundy:#7a1a3c;
  --burgundy-dark:#5e1230;
  --green:#7ea63a;
  --green-dark:#5f8a26;
  --green-active:#5d6a2a;
  --ink:#3f3f3f;
  --text:#555;
  --rule:#dcdcdc;
  --band:#e3e3e3;
  --footer:#2b2b2b;
  --disc:#5d5a5a;
}
*{box-sizing:border-box;margin:0;padding:0}
html,body{width:1010px;height:1200px;overflow:hidden;background:#fff}
body{position:relative;font-family:"Arimo",Arial,sans-serif;color:var(--text);font-size:10px}
.abs{position:absolute}
.heading{font-family:"Open Sans",Arial,sans-serif;font-weight:600;font-stretch:87%;color:var(--ink);font-size:19px;letter-spacing:-.2px;white-space:nowrap}

/* header */
.brand{left:120px;top:19px;width:139px;height:69px;background:var(--burgundy);color:#fff;font-family:"Open Sans",sans-serif;font-weight:600;padding:14px 0 0 18px}
.brand .name{font-size:19px;line-height:20px;letter-spacing:-.3px}
.brand .sub{font-size:11px;line-height:13px;margin-left:18px}
.notice{left:504px;top:30px;width:387px;height:48px;background:var(--burgundy);border-radius:4px;color:#fff;font-family:"Open Sans",sans-serif;font-size:9.3px;line-height:19px;padding:5px 0 0 8px;letter-spacing:-.1px}
.notice:after{content:"";position:absolute;left:24px;bottom:-8px;border:8px solid transparent;border-bottom:0;border-top-color:var(--burgundy)}

/* nav */
.nav{left:0;top:107px;width:1010px;height:36px;background:linear-gradient(#8ab443,var(--green) 50%,#6f9a2e);border-top:1px solid #a3c56a;border-bottom:1px solid var(--green-dark)}
.nav a{position:absolute;top:0;height:34px;line-height:34px;text-align:center;color:#fff;text-decoration:none;font-family:"Open Sans",sans-serif;font-weight:600;font-size:10.5px;border-right:1px solid #6c9330}
.nav a.active{background:var(--green-active)}
.search{left:668px;top:4px;width:219px;height:26px;background:#f5f7ef;border:1px solid #cfe0ad}
.search .btn{position:absolute;right:0;top:-1px;width:29px;height:26px;background:var(--green-dark);border:1px solid #9dbd66}

/* hero */
.hero{left:0;top:143px;width:1010px;height:297px;background:linear-gradient(90deg,#d9cfc8 0%,#c9b6a6 25%,#a08470 45%,#7b6454 55%,#b7c6d6 70%,#e3dcd2 85%,#2c2a28 100%)}
.hero-copy{left:120px;top:216px;width:340px}
.hero-copy h1{font-family:"Open Sans",sans-serif;font-weight:400;font-size:25px;color:var(--burgundy);letter-spacing:-.4px;line-height:30px}
.hero-copy h2{font-family:"Open Sans",sans-serif;font-weight:400;font-size:20px;color:var(--burgundy);line-height:26px;margin-top:4px;letter-spacing:-.3px}
.hero-copy p{font-family:"Open Sans",sans-serif;font-size:11.3px;line-height:19px;color:#4a4440;margin-top:9px;letter-spacing:-.2px}
.dots{left:120px;top:358px;display:flex;gap:6px}
.dots i{width:10px;height:10px;border-radius:50%;background:#8f8f8f;border:1px solid #777}
.dots i.on{background:var(--burgundy);border-color:var(--burgundy-dark)}
.hero-line{left:32px;top:440px;width:787px;height:1px;background:#bdbdbd}

/* arrows */
.arrows{display:flex;gap:1px}
.arrows span{width:18px;height:17px;background:#1f1f1f;color:#e06b1a;font-size:9px;line-height:17px;text-align:center;font-family:Arial,sans-serif}
.rule{height:1px;background:var(--rule)}

/* welcome */
.welcome-photo{left:120px;top:515px;width:205px;height:175px;background:linear-gradient(135deg,#cfd6d2,#8c8f8a 40%,#2d2b2c 75%,#5a5a5a)}
.welcome-text{left:332px;top:512px;width:285px;font-size:9.8px;letter-spacing:-.15px;line-height:12.8px;text-align:justify}
.welcome-text h3{font-weight:400;font-size:10.5px;letter-spacing:0;color:var(--burgundy);margin-bottom:12px;text-align:left}
.welcome-text p{margin-bottom:12px}

/* testimonials */
.test-photo{left:657px;top:518px;width:78px;height:67px;background:linear-gradient(135deg,#c9c6c0,#b88d74 45%,#6a5548 75%,#9ea4a8)}
.test-side{left:742px;top:518px;width:149px;font-size:9.6px;letter-spacing:-.2px;line-height:13.4px;text-align:justify}
.test-body{left:655px;top:598px;width:236px;font-size:10px;line-height:13.4px;text-align:justify}
.test-sign{left:655px;top:664px;font-size:10px;line-height:13.4px}
.test-sign .who{color:var(--green)}

.divider{left:120px;top:717px;width:771px;height:4px;background:#e0e0dc;border-top:1px solid #cfcfca}
.vsep{width:4px;background:#e0e0dc;border-left:1px solid #cfcfca}

/* services */
.svc-intro{left:120px;top:795px;width:237px;font-size:10px;line-height:14.4px;text-align:justify}
.svc-list{left:122px;top:848px;list-style:none;font-size:10px}
.svc-list li{height:29px;display:flex;align-items:center;gap:8px;color:#333}
.svc-list li:before{content:"›";width:9px;height:9px;border-radius:50%;background:#1e1e1e;color:#fff;font-size:9px;line-height:8px;text-align:center}

/* opportunities */
.opp{left:379px;width:255px;height:58px}
.opp .date{position:absolute;left:0;top:0;width:57px;height:57px;border-radius:50%;background:var(--disc);color:#fff;font-family:"Open Sans",sans-serif;font-size:15.5px;line-height:19px;text-align:center;padding-top:9px}
.opp h4{position:absolute;left:65px;top:6px;font-weight:400;font-size:9.8px;color:#333;white-space:nowrap}
.opp p{position:absolute;left:65px;top:24px;font-size:7.6px;color:#666;white-space:nowrap}
.opp a{position:absolute;left:65px;top:39px;font-size:8.4px;color:var(--burgundy);text-decoration:none}
.pager{left:442px;top:997px;display:flex;gap:3px}
.pager i{width:13px;height:13px;border-radius:50%;background:#c8c8c8;border:1px solid #aaa;position:relative}
.pager i:after{content:"";position:absolute;top:3px;left:4px;border:3px solid transparent}
.pager i.prev:after{border-right:4px solid var(--burgundy);left:1px}
.pager i.next:after{border-left:4px solid var(--burgundy);left:4px}

/* events */
.video{left:656px;top:800px;width:236px;height:190px;background:linear-gradient(90deg,#d6dadd,#ffffff 35%,#7f868c 60%,#2b2b2f 80%,#e2e0de)}
.player{left:656px;top:990px;width:236px;height:14px;background:linear-gradient(#fafafa,#d8d8d8);border:1px solid #aaa;font-size:7px;font-weight:700;font-family:Arial,sans-serif;color:#222}

/* clients */
.clients{left:0;top:1034px;width:1010px;height:93px;background:var(--band);box-shadow:0 3px 3px rgba(0,0,0,.35)}
.clients-label{left:164px;top:1075px;font-family:"Open Sans",sans-serif;font-size:11px;color:#2e2e2e}
.client-name{top:1070px;font-family:"Open Sans",sans-serif;font-weight:600;font-size:14px;color:#6a2438;white-space:nowrap}

/* footer */
.footer{left:0;top:1150px;width:1010px;height:50px;background:var(--footer)}
.copyright{left:121px;top:1169px;font-size:9.5px;color:var(--green)}
.social{top:1164px;width:23px;height:23px;border-radius:50%;background:#3a3a3a;border:1px solid #444}
</style>
</head>
<body>

<header>
  <div class="abs brand"><div class="name">bluefern</div><div class="sub">Business Services</div></div>
  <div class="abs notice">Current Opportunities : There are often a number of opportunities available at Bluefern.<br>Here are the latest ones. Be sure to get your application form in before the closing date!</div>
</header>

<nav class="abs nav">
  <a class="active" style="left:121px;width:97px">HOME</a>
  <a style="left:218px;width:143px">ABOUT BLUEFERN</a>
  <a style="left:361px;width:103px">SERVICES</a>
  <a style="left:464px;width:101px">CAREERS</a>
  <a style="left:565px;width:102px;border-right:0">CONTACT</a>
  <div class="abs search">
    <div class="btn"><svg width="27" height="24" viewBox="0 0 27 24"><circle cx="12" cy="10" r="4" fill="none" stroke="#fff" stroke-width="1.6"/><line x1="15" y1="13" x2="19" y2="17" stroke="#fff" stroke-width="2"/></svg></div>
  </div>
</nav>

<section>
  <div class="abs hero" role="img" aria-label="Photo of smiling colleagues sitting together in a meeting"></div>
  <div class="abs hero-copy">
    <h1>Typinon habent claritatem</h1>
    <h2>Duis autem vel eum iriure dolor</h2>
    <p>Ut wisi enim ad minim veniam, quis nostrud exerci tation ullamcor per suscipit lobortis nisl ut aliquip ex ea commodo consequat. Dus autem vel eum iriure dolor.</p>
  </div>
  <div class="abs dots"><i class="on"></i><i></i><i></i><i></i></div>
  <div class="abs hero-line"></div>
</section>

<section>
  <h2 class="abs heading" style="left:121px;top:458px">WELCOME!</h2>
  <div class="abs rule" style="left:120px;top:496px;width:497px"></div>
  <div class="abs welcome-photo" role="img" aria-label="Photo of two businesswomen working at a laptop"></div>
  <div class="abs welcome-text">
    <h3>Delivering IT Excellence</h3>
    <p>Welcome to Bluefern Business Services, an emerging provider of global IT consulting and software services. We are part of the Marlow Goods group, a family run business and the world's largest multi-channel home delivery wine merchant...</p>
    <p>Nemo enim ipsam voluptatem quia voluptas sit aspernatur aut odit aut fugit,</p>
    <p style="margin-top:24px">Services, an emerging provider of global IT consulting and software services. We are part of the Marlow Goods group, a family run business and the world's largest multi-channel home deliv-</p>
  </div>

  <h2 class="abs heading" style="left:657px;top:458px">TESTIMONIALS</h2>
  <div class="abs arrows" style="left:853px;top:463px"><span>&lt;</span><span>&gt;</span></div>
  <div class="abs rule" style="left:655px;top:496px;width:236px"></div>
  <div class="abs test-photo" role="img" aria-label="Portrait photo of the client quoted"></div>
  <div class="abs test-side">Marlow Goods IT landscape. Current plans to strategically transform this landscape to a single set of global systems are underway, across all locations and all</div>
  <div class="abs test-body">Marlow Goods IT landscape. Current plans to strategically transform this landscape to a single set of global systems are underway, across all locations and all four continents.</div>
  <div class="abs test-sign">Thanks<br><span class="who">Daniel</span></div>
</section>

<div class="abs divider"></div>

<section>
  <h2 class="abs heading" style="left:120px;top:741px">SERVICES</h2>
  <div class="abs arrows" style="left:319px;top:747px"><span>&lt;</span><span>&gt;</span></div>
  <div class="abs rule" style="left:120px;top:780px;width:236px"></div>
  <p class="abs svc-intro">The services we provide enable the businesses we support to efficiently manage key functions, including order management.</p>
  <ul class="abs svc-list">
    <li>Packaged Applications</li>
    <li>Enterprise Application Integration</li>
    <li>Digital Commerce</li>
    <li>Application Development &amp; Maintenance</li>
    <li>Multiple versions of Corvex Commerce</li>
    <li>Ledgerline AX 2009</li>
  </ul>
  <div class="abs vsep" style="left:370px;top:740px;height:270px"></div>

  <h2 class="abs heading" style="left:385px;top:741px">LATEST OPPORTUNITIES</h2>
  <div class="abs arrows" style="left:587px;top:747px"><span>&lt;</span><span>&gt;</span></div>
  <div class="abs rule" style="left:385px;top:780px;width:238px"></div>
  <article class="abs opp" style="top:789px"><div class="date">Jan<br>07</div><h4>Software Developers/Programmer Analysts</h4><p>AX We are looking for a AX Software Developer join...</p><a>read more &gt;&gt;</a></article>
  <article class="abs opp" style="top:859px"><div class="date">Jan<br>07</div><h4>Software Developers/Programmer Analysts</h4><p>AX We are looking for a AX Software Developer join...</p><a>read more &gt;&gt;</a></article>
  <article class="abs opp" style="top:929px"><div class="date">Jan<br>07</div><h4>Software Developers/Programmer Analysts</h4><p>AX We are looking for a AX Software Developer join...</p><a>read more &gt;&gt;</a></article>
  <div class="abs pager"><i class="prev"></i><i class="next"></i></div>
  <div class="abs vsep" style="left:637px;top:740px;height:270px"></div>

  <h2 class="abs heading" style="left:656px;top:741px">RECENT EVENTS</h2>
  <div class="abs arrows" style="left:853px;top:747px"><span>&lt;</span><span>&gt;</span></div>
  <div class="abs rule" style="left:655px;top:780px;width:236px"></div>
  <div class="abs video" role="img" aria-label="Video still of a presenter leading a team meeting at a whiteboard"></div>
  <svg class="abs" style="left:758px;top:880px" width="40" height="40" viewBox="0 0 40 40"><circle cx="20" cy="20" r="19" fill="rgba(40,40,40,.6)" stroke="#fff" stroke-width="1.5"/><path d="M15 11 L29 20 L15 29 Z" fill="#fff"/></svg>
  <div class="abs player">
    <span style="position:absolute;left:4px;top:1px">▶</span>
    <span style="position:absolute;left:16px;top:2px">00:01</span>
    <span style="position:absolute;left:47px;top:5px;width:110px;height:3px;background:#888"></span>
    <span style="position:absolute;left:163px;top:2px">100 %</span>
    <span style="position:absolute;left:196px;top:1px">▣</span>
    <span style="position:absolute;left:210px;top:2px">◂ıılll</span>
  </div>
</section>

<section>
  <div class="abs clients"></div>
  <svg class="abs" style="left:120px;top:1063px" width="25" height="25" viewBox="0 0 25 25"><rect x="1" y="0" width="7" height="25" fill="#8cc63f"/><rect x="9" y="6" width="7" height="19" fill="#4a90d9"/><rect x="17" y="11" width="7" height="14" fill="#f08a24"/></svg>
  <div class="abs clients-label">OUR CLIENTS</div>
  <div class="abs" style="left:252px;top:1060px;width:1px;height:42px;background:#c8c8c8"></div>
  <div class="abs client-name" style="left:288px">Coastal Vine</div>
  <div class="abs client-name" style="left:422px">Cellar Nova</div>
  <div class="abs client-name" style="left:553px">Harvest Table</div>
  <div class="abs client-name" style="left:697px">Marlow Goods</div>
  <div class="abs client-name" style="left:815px">Tidewell Wines</div>
</section>

<footer>
  <div class="abs footer"></div>
  <div class="abs copyright">© 2014 bluefernbs.. All Rights Reserved.</div>
  <div class="abs social" style="left:778px"></div>
  <div class="abs social" style="left:807px"></div>
  <div class="abs social" style="left:837px"></div>
  <div class="abs social" style="left:867px"></div>
</footer>

</body>
</html>
```